Website front end design for an education nonprofit

This project involves design and development of the website front end (i.e., Web user interface and user experience design) for TAVO Sphere, a nonprofit initiative for developing an online platform for basic English language instruction, especially targeted toward underprivileged, non-native English speaking populations.

More about us: We are a team of educators, researchers and engineers passionate about this cause and would like to invite talented, creative web developers to join us in this effort to create positive social impact! Please send a personal message to the project owner for the executive summary to get more information about our initiative, big picture vision and the team.

TAVO Sphere website front end (UI/UX) design
Our key goals for this project are to develop an impressive Drupal-based front end for our website as well as to find really talented and creative web/UI/UX designers-cum-developers who are experts in the state-of-the-art web technologies, and are passionate about the cause of global online basic education. At the end of this project, we hope to have long term engagement with the selected developer(s) for our future website design and development needs.

Here are some preliminary guidelines on the TAVO Sphere website front end framework as envisioned by us so far. Please note that we would very much encourage creative ideas and mock-ups from the developers.

1. Current platform: Our website prototype back-end uses Drupal CMS (we plan to continue using Drupal CMS) and at the moment, a toy front-end is based on the Drupal Skeleton platform for its simplicity, clean UI and mobile device friendliness. The web developer / designer can choose any Drupal front end as a starting point or come up with a new Drupal template that meets our requirements below. Prior experience and expertise on Drupal would be great.

2. Audience profile: While the primary audience for the website is expected to be young kids (6-10 years) not very familiar with English, the secondary audience also includes adults interested in basic English language skills. So the overall goal is to have simple, uncluttered / clean, elegant and lightweight (think loading time as well as mobile device friendliness) interface that is extremely intuitive and easy to navigate, is artistic and aesthetically appealing to a wide audience (especially the non-native English speaking populations). The most important point is that our target audience should feel welcome with the clean, crisp look and easy, user-centric navigation, and should in no case feel overwhelmed (say with too much text or clutter on the front page).

3. Front page: Here is a currently envisioned preliminary sketch of the website front page (very much open for refinement and improvements)
a. The top “menu bar” part of the landing page will have our organization name and logo along with (or above) the top menu bar with the following links and sub-links
i. “Learn” link with sub-menu of all our content sections (World learning, Basic sentence learning, Classic short stories, Picture Dictionary)
ii. “About” links with information about us (sub-menu entries: About TAVO Sphere, Team, Supporters, Contributors)
iii. “Contribute” link with sub-menu entries Donate, Volunteer
iv. Menu entries towards the right side: “Login / sign up” followed by
v. “Search” with space to enter the search phrase
b. The middle “main page content” part of the page is where we would have entry points to our main content categories. The portion is envisioned to be graphical, with big blocks (images) as links to our content categories. The current categories (to start with) include 1. Word learning, 2. Basic sentence learning, and 3. Classic stories. We welcome creative ideas to represent these content categories in an appealing and elegant way (for example, these content categories could be portrayed as closed double doors that lead to the pages with the content. We would like to have placeholders for appropriate image links to different content categories – we should be able to put appropriate images or change them as we come up with new ideas that would work best with our target audience). The categories would change and grow as our content evolves, hence the core idea is to build a flexible framework that readily allows for expansion as well as customization.
c. The bottom menu / links bar portion of the landing page will have a list of links that are not included at the top. Examples include (with flexibility needed to add more when needed)
i. “Help”: this leads to a new page with FAQ, How to use
ii. “Contact us” link to a web contact form page
iii. “For Teachers” link to a page with information such as how to use, tips, pilot programs,
iv. “Volunteer” link to page with links such as Donate, Volunteer
v. “Contributors” that would link to a page with information about our Artists, Teachers, Writers, Developers etc.
vi. “Jobs” would link to a jobs page
vii. “Blog” would lead to our blog page
viii. “User stories” link to pages with feedback that we obtain from the users about how the content has helped them,
ix. Web 2.0 placeholders for social media (to be added later)

d. The footer of the website should include text “2013 TAVO Sphere, All rights reserved.”

4. The middle block of the front page is the largest in screen real estate and perhaps the most challenging part that requires much creativity and thought on the UI/UX design aspect – the content pages pointed to by the section links on the middle portion of the front page are also being designed.

5. Color preference is towards soft, elegant (think grays, whites, light blues, other light colors) web safe colors. No harsh (too bright, garish) colors.

6. Fonts preference Nice, clean looking fonts (Arial alright) compatible across browsers.

7. Portability and robustness of the front page layout for different platforms should be carefully considered. Although our first launch target platform is PC (where cross browser compatibility is important), this would very soon be followed by mobile devices such as tablets and smartphones given their prevalence across the globe. This mobile friendly design or easy portability to mobile platforms with little work requirement should be considered as a design requirement.

8. Front page as a framework for the complete website: Note that the top and the bottom portions of the front page are envisioned be used as a common template / frame across all the pages of our website – the middle portion would be used to show our content on the other pages of our website.

9. UX: For the UI/UX design, it is critical to keep in mind key qualities such as ease of use, simplicity, elegance and artistic appeal. Some specific points to keep in mind: (1) the major portion of the target audience would be new to English and (2) young children are expected to be the primary audience but we want the website to appeal to adults interested in learning as well, and (3) we need the website to work even with relatively slow Internet speeds (for underdeveloped / developing regions especially), should always be kept in mind. HTML5 compliance ideas are encouraged.

10. Strictly not desired: Typical corporate feel seen in many webpages, blocky graphics, dull and uninviting overall look with no personality, Flash type effects, harsh colors.

11. Creativity and imagination necessary: We would like to reiterate that the designer/developer has complete freedom to re-imagine the front page considering the above requirements and get back with ideas for an inspiring layout that presents the content outlined above in an intuitive format, carefully considering our target audience.

A note: As a rule, we will always make sure that our developers and artists get proper credit for their work and are recognized and acknowledged by everyone visiting our website.

Expected deliverables:
Website design psd files AND coded webpage / Drupal template: the corresponding source code and all the required libraries, images etc would be required with minimal documentation / pointers on how to make changes and customizations.

Interested developers are encouraged to first send us preliminary prototype Design for the front page to get feedback on whether their approach and style is in line with our needs and preferences. We will suggest the developers to proceed further if the team thinks there is some potential for a match (of course, the final determination would be from the pool of shortlisted submissions) – otherwise, in case the team does not see potential for a match with our needs or if we have already received multiple submissions that are comparatively more closely aligned with our vision for the website, we'd prefer to be respectful of the developers’ time and effort by requesting them not to proceed further.

Please consider this effort as your contribution to an important social cause of global and accessible online education and not a commercial enterprise (our passion for making a positive impact is what is driving the TAVO Sphere nonprofit team to undertake this initiative!). We would like to invite you to join us in this effort!

Project Deadline Extended
Reason: Due to requests from interested designers, we are extending the deadline. Looking forward to receiving many other creative designs!

Please see the project brief.

Real Estate

• Please see the project brief.

```html
<!DOCTYPE html>
<html lang="en">
<head>
<meta charset="utf-8">
<title>TAVO Sphere</title>
<link href="https://fonts.googleapis.com/css2?family=Open+Sans:wght@400;600;700&display=swap" rel="stylesheet">
<style>
:root{
  --blue:#2a9fd8;
  --blue-dark:#1f86bb;
  --ink:#333;
  --muted:#777;
  --soft:#f1f1f1;
  --line:#dcdcdc;
  --footer:#3b3b3b;
  --footer-deep:#2a2a2a;
  --footer-text:#c9c9c9;
  --panel:rgba(20,24,28,.82);
}
*{box-sizing:border-box;margin:0;padding:0}
html,body{width:867px;height:1200px;overflow:hidden}
body{font-family:"Open Sans",Arial,sans-serif;color:var(--ink);background:#fff;font-size:11px;line-height:1.5}
.wrap{width:770px;margin:0 auto;position:relative}

/* header */
.site-header{height:80px}
.site-header .wrap{display:flex;align-items:center;height:80px}
.brand{font-size:24px;font-weight:700;color:var(--blue);letter-spacing:-.3px;width:232px}
.main-nav{display:flex;gap:26px;font-size:13px;width:215px}
.main-nav a{color:var(--ink);text-decoration:none}
.search{width:145px;height:24px;border:1px solid var(--line);display:flex;align-items:center;justify-content:space-between;padding:0 7px;color:#aaa;font-size:10px;margin-right:22px}
.btn{background:var(--blue);color:#fff;font-size:11px;font-weight:600;height:24px;display:flex;align-items:center;justify-content:center;border-radius:2px}
.btn.signup{width:58px;margin-right:16px}
.btn.login{width:72px}

/* hero */
.hero{height:394px;position:relative;background:linear-gradient(135deg,#6f8a4a 0%,#9c7a5e 30%,#3e4a5a 55%,#2b2e35 75%,#7a6e62 100%)}
.hero-arrow{position:absolute;top:160px;width:24px;height:24px;border-radius:50%;background:rgba(0,0,0,.55)}
.hero-arrow.prev{left:58px}
.hero-arrow.next{right:58px}
.hero-arrow svg{width:24px;height:24px}
.categories{position:absolute;left:0;right:0;bottom:26px;display:flex;justify-content:center;gap:4px}
.category{width:232px;height:90px;background:var(--panel);color:#fff;padding:13px 14px}
.category-head{display:flex;align-items:center;gap:8px;margin-bottom:8px}
.category-head svg{width:26px;height:26px;flex:none}
.category h3{font-size:12px;font-weight:700;letter-spacing:.2px;text-transform:uppercase}
.category p{font-size:9.5px;color:#d6d6d6;line-height:1.45}

/* welcome */
.welcome{background:var(--soft);height:236px;padding-top:28px}
.section-title{font-size:17px;font-weight:600;color:var(--ink);margin-bottom:14px}
.section-title span{color:var(--blue)}
.welcome-body{display:flex}
.welcome-photo{width:153px;height:126px;background:linear-gradient(160deg,#c9b8a5,#8f9fae 60%,#e3e0da);flex:none}
.welcome-text{width:231px;margin-left:14px;color:#666;font-size:10.5px;line-height:1.6}
.video{width:252px;height:138px;margin-left:auto;margin-top:-30px;position:relative;background:linear-gradient(150deg,#b9c3cc,#6f7c88 55%,#4d5660)}
.video .play{position:absolute;left:50%;top:42%;transform:translate(-50%,-50%);width:34px;height:34px}
.video-caption{position:absolute;left:0;right:0;bottom:0;height:26px;background:rgba(0,0,0,.6);color:#fff;font-size:11px;font-weight:600;padding:5px 10px}

/* blog */
.blog{padding-top:26px;height:256px}
.blog .section-title{font-size:14px;font-weight:700;text-transform:uppercase}
.posts{display:flex;gap:16px}
.post{width:181px}
.post-photo{height:105px;margin-bottom:7px}
.post:nth-child(1) .post-photo{background:linear-gradient(150deg,#a8b4c2,#5b6877)}
.post:nth-child(2) .post-photo{background:linear-gradient(150deg,#e7d6c3,#b38a6b)}
.post:nth-child(3) .post-photo{background:linear-gradient(150deg,#3d5a8a,#b73a3a 60%,#e9e2dc)}
.post:nth-child(4) .post-photo{background:linear-gradient(150deg,#d9cab8,#8c6e58)}
.post-date{color:var(--blue);font-size:9.5px}
.post p{color:#777;font-size:9.5px;line-height:1.5;margin:2px 0 6px}
.more{font-size:9px;font-weight:700;color:var(--ink);letter-spacing:.3px}

/* footer */
.site-footer{background:var(--footer);height:214px;padding-top:22px;color:var(--footer-text)}
.footer-cols{display:flex}
.footer-col h4{color:#fff;font-size:12px;font-weight:600;margin-bottom:5px}
.footer-col ul{list-style:none;font-size:9.5px;line-height:1.75}
.col-popular{width:164px}
.col-learn{width:182px}
.col-outreach{width:208px}
.col-news{width:216px}
.field{height:20px;border:1px solid #555;background:#fff;color:#999;font-size:9px;padding:3px 6px;margin-bottom:6px;width:150px}
.submit{background:var(--blue);color:#fff;font-size:8.5px;font-weight:700;width:48px;height:18px;display:flex;align-items:center;justify-content:center;margin-left:102px;margin-bottom:12px}
.social{display:flex;gap:8px;margin-top:4px}
.social span{width:20px;height:20px;border-radius:50%;background:#5a5a5a}
.copyright{background:var(--footer-deep);height:20px;color:#aaa;font-size:9px;line-height:20px}
</style>
</head>
<body>

<header class="site-header">
  <div class="wrap">
    <div class="brand">TAVO Sphere</div>
    <nav class="main-nav"><a href="#">Learn</a><a href="#">About</a><a href="#">Contribute</a></nav>
    <div class="search"><span>Search</span>
      <svg width="10" height="10" viewBox="0 0 10 10"><circle cx="4" cy="4" r="3" fill="none" stroke="#999" stroke-width="1.3"/><line x1="6.2" y1="6.2" x2="9" y2="9" stroke="#999" stroke-width="1.3"/></svg>
    </div>
    <div class="btn signup">Sign up</div>
    <div class="btn login">Login</div>
  </div>
</header>

<section class="hero" role="img" aria-label="Young students studying together on a laptop outdoors">
  <div class="hero-arrow prev"><svg viewBox="0 0 24 24"><path d="M14 7l-5 5 5 5" fill="none" stroke="#fff" stroke-width="2"/></svg></div>
  <div class="hero-arrow next"><svg viewBox="0 0 24 24"><path d="M10 7l5 5-5 5" fill="none" stroke="#fff" stroke-width="2"/></svg></div>
  <div class="categories">
    <div class="category">
      <div class="category-head">
        <svg viewBox="0 0 26 26"><path d="M3 6h8a2 2 0 0 1 2 2v13a2 2 0 0 0-2-2H3zM23 6h-8a2 2 0 0 0-2 2v13a2 2 0 0 1 2-2h8z" fill="none" stroke="#fff" stroke-width="1.6"/></svg>
        <h3>Word Learning</h3>
      </div>
      <p>Practice everyday words with sound and picture cards for all ages.</p>
    </div>
    <div class="category">
      <div class="category-head">
        <svg viewBox="0 0 26 26"><path d="M2 10l11-5 11 5-11 5z" fill="#fff"/><path d="M7 13v5c3 2 9 2 12 0v-5" fill="none" stroke="#fff" stroke-width="1.6"/></svg>
        <h3>Basic Sentence Learning</h3>
      </div>
      <p>Build short sentences step by step with friendly guided lessons.</p>
    </div>
    <div class="category">
      <div class="category-head">
        <svg viewBox="0 0 26 26"><path d="M21 3C12 5 7 12 5 23M21 3c0 8-6 13-12 14" fill="none" stroke="#fff" stroke-width="1.6"/></svg>
        <h3>Classic Stories</h3>
      </div>
      <p>Read timeless tales retold in simple English for young readers.</p>
    </div>
  </div>
</section>

<section class="welcome">
  <div class="wrap">
    <h2 class="section-title">Welcome to <span>TAVO Sphere</span></h2>
    <div class="welcome-body">
      <div class="welcome-photo" role="img" aria-label="Children learning at a laptop"></div>
      <p class="welcome-text">We are a team of educators and engineers building a free place to learn basic English. Our lessons use pictures, sounds and short words so every child can start with ease. Adults are welcome too, and every page loads fast even on slow connections across the world.</p>
      <div class="video" role="img" aria-label="Video preview of a learner at a computer">
        <svg class="play" viewBox="0 0 34 34"><circle cx="17" cy="17" r="16" fill="rgba(0,0,0,.5)" stroke="#fff" stroke-width="1.5"/><path d="M13 10l11 7-11 7z" fill="#fff"/></svg>
        <div class="video-caption">Online Learning Material</div>
      </div>
    </div>
  </div>
</section>

<section class="blog">
  <div class="wrap">
    <h2 class="section-title">Blog Posts</h2>
    <div class="posts">
      <article class="post">
        <div class="post-photo" role="img" aria-label="Boy writing at a desk"></div>
        <div class="post-date">Posted on July 26, 2013</div>
        <p>New picture cards help young learners name the things they see at home.</p>
        <div class="more">LEARN MORE</div>
      </article>
      <article class="post">
        <div class="post-photo" role="img" aria-label="Girl reading a book"></div>
        <div class="post-date">Posted on July 26, 2013</div>
        <p>Teachers share simple games that turn a short word list into play.</p>
        <div class="more">LEARN MORE</div>
      </article>
      <article class="post">
        <div class="post-photo" role="img" aria-label="Student in front of a flag"></div>
        <div class="post-date">Posted on July 26, 2013</div>
        <p>Our volunteers met families to hear how lessons fit their daily life.</p>
        <div class="more">LEARN MORE</div>
      </article>
      <article class="post">
        <div class="post-photo" role="img" aria-label="Young girl smiling over a notebook"></div>
        <div class="post-date">Posted on July 26, 2013</div>
        <p>A short guide on reading aloud together with a child every evening.</p>
        <div class="more">LEARN MORE</div>
      </article>
    </div>
  </div>
</section>

<footer class="site-footer">
  <div class="wrap footer-cols">
    <div class="footer-col col-popular">
      <h4>Popular</h4>
      <ul><li>Help</li><li>Contact us</li><li>For teachers</li><li>Volunteer</li><li>Contributors</li><li>Jobs</li><li>Blog</li><li>User stories</li></ul>
    </div>
    <div class="footer-col col-learn">
      <h4>Learn</h4>
      <ul><li>Word learning</li><li>Basic sentence learning</li><li>Classic short stories</li><li>Picture Dictionary</li></ul>
      <h4 style="margin-top:6px">About</h4>
      <ul><li>About TAVO Sphere</li><li>Team</li><li>Supporters</li></ul>
    </div>
    <div class="footer-col col-outreach">
      <h4>Outreach</h4>
      <ul><li>Self guided study</li><li>Leadership 2013</li><li>Feedback materials</li><li>Webinar summit 2013</li><li>Ready to read: part one of three</li></ul>
    </div>
    <div class="footer-col col-news">
      <h4>Newsletter Signup</h4>
      <div class="field">Name</div>
      <div class="field">Email id</div>
      <div class="submit">SUBMIT</div>
      <h4>Follow us</h4>
      <div class="social"><span></span><span></span><span></span></div>
    </div>
  </div>
</footer>
<div class="copyright"><div class="wrap">Copyrights 2013, All Rights Reserved.</div></div>

</body>
</html>
```